Brightwell Supports

We need an updated website that captures the comprehensive services and supports we provide to persons with developmental disabilities. We need a website design that educates families about the services we provide. We would also need a website that is user-friendly so that we could periodically update training schedules and ongoing programming.

• Thank you for submitting designs.  A few things I am hoping to see offered in the website:
• Front page highlights the services we offer (host homes, family caregiver, day program, employment program, SLS program, supported apartment program, behavior/clinical program)
• Front page also highlights any new programs we want to make prominent:  family caregiver, future restaurant employment openings, etc...
• Interactive Training Calendar
• Employee Resources page (link to carevo, email login, etc.)
• Uniform provider application for host home providers
• Information on agency - history, goals, etc.
• Contact Information/Location

 

Fun things to include:

• Client Highlights (featuring a client story each month, etc...)
• Employee highlights (featuring a staff member...)
• link to other Brightwell business pages (Brightwell Therapy and Brightwell Restaurant)

```html
<!DOCTYPE html>
<html lang="en">
<head>
<meta charset="utf-8">
<title>Brightwell Supports</title>
<link href="https://fonts.googleapis.com/css2?family=Open+Sans:wght@400;600&family=Arimo:wght@400&display=swap" rel="stylesheet">
<style>
:root{
  --brand:#8b2a2b;
  --brand-dark:#6f1f20;
  --ink:#333;
  --muted:#777;
  --nav:#2a2a2a;
  --footer:#1f1f1f;
  --footer-base:#151515;
  --panel:#ececec;
  --accent:#e8443a;
}
*{box-sizing:border-box;margin:0;padding:0}
html,body{width:803px;height:1200px;overflow:hidden}
body{background:var(--brand);font-family:"Open Sans",sans-serif;color:var(--ink);position:relative}
.page{position:absolute;left:76px;top:0;width:651px;height:1200px;background:#fff}
.abs{position:absolute}
.call{left:24px;top:20px;display:flex;gap:10px;align-items:center}
.call small{display:block;font-size:9px;color:#222}
.call strong{display:block;font-size:10.5px;font-weight:400;color:#222}
.logo{left:215px;top:14px;width:220px;height:46px;display:flex;align-items:center;justify-content:center;gap:7px;white-space:nowrap}
.logo .mark{width:22px;height:22px;border-radius:50%;background:var(--brand);flex:none}
.logo span{font-size:15px;font-weight:600;color:var(--brand)}
.social{right:22px;top:24px;display:flex;gap:5px}
.social i{width:19px;height:19px;border-radius:50%;background:var(--brand);display:block}
.nav{left:12px;top:67px;width:628px;height:43px;background:var(--nav);display:flex;align-items:center;justify-content:space-between;padding-right:14px}
.nav a{flex:none;white-space:nowrap;color:#fff;text-decoration:none;font-size:9px;height:43px;line-height:43px}
.nav a.active{background:var(--brand);padding:0 14px}
.hero{left:12px;top:110px;width:628px;height:292px;background:linear-gradient(160deg,#9a9fa6 0%,#767c84 45%,#4a4d52 80%,#3a3b3e 100%)}
.hero .rock{position:absolute;right:0;top:0;width:260px;height:292px;background:linear-gradient(200deg,#5a5b5e,#2e2f31);clip-path:polygon(55% 0,100% 10%,100% 100%,30% 100%,20% 55%,40% 25%)}
.hero .caption{position:absolute;left:0;bottom:0;width:100%;height:54px;background:rgba(50,50,50,.55);color:#fff;font-size:17.5px;text-align:center;line-height:54px;white-space:nowrap}
.hero .arrow{position:absolute;top:133px;width:26px;height:26px;border-radius:50%;border:2px solid #fff;background:rgba(0,0,0,.25)}
h2{position:absolute;left:0;width:651px;text-align:center;color:var(--brand);font-size:16.5px;font-weight:600}
.intro{left:12px;top:450px;width:628px;font-size:8px;line-height:15px;color:var(--muted);text-align:center}
.values{left:12px;top:550px;width:628px;height:208px;background:var(--panel);border:1px solid #ddd}
.card{position:absolute;top:18px;width:131px;height:170px;background:#fff;border:1px solid #ddd;text-align:center}
.card .ph{margin:2px;height:95px}
.card h3{font-size:9px;font-weight:400;color:var(--brand);margin-top:9px;white-space:nowrap}
.card p{font-size:7.2px;line-height:13px;color:#999;padding:5px 5px 0}
.chev{position:absolute;top:92px;font-size:18px;color:#bbb}
.support{position:absolute;width:200px;display:flex;gap:10px}
.support svg{flex:none}
.support h4{font-size:9px;font-weight:600;margin-bottom:5px;color:#222;white-space:nowrap}
.support p{font-size:7.5px;line-height:12.5px;color:#666}
.footer{left:0;top:986px;width:651px;height:157px;background:var(--footer);font-family:"Arimo",sans-serif;color:#ddd}
.footer h5{position:absolute;top:17px;font-size:11.5px;font-weight:400;color:#fff}
.footer ul{position:absolute;list-style:none;font-size:8.5px;line-height:15px}
.footer li{display:flex;gap:8px}
.footer a{color:var(--accent);text-decoration:none}
.footer .time{color:var(--accent);font-size:7px}
.thumb{width:34px;height:34px;border:1px solid #555;flex:none}
.base{left:0;top:1143px;width:651px;height:57px;background:var(--footer-base);font-family:"Arimo",sans-serif}
.base p{position:absolute;left:12px;top:24px;font-size:7.5px;color:#fff}
.base .ring{position:absolute;top:16px;width:25px;height:25px;border-radius:50%;border:1px solid var(--accent)}
</style>
</head>
<body>
<div class="page">
  <div class="abs call">
    <svg width="16" height="22" viewBox="0 0 16 22"><rect x="1" y="1" width="14" height="20" rx="2" fill="none" stroke="#8b2a2b" stroke-width="1.5"/><line x1="1" y1="16" x2="15" y2="16" stroke="#8b2a2b"/></svg>
    <div><small>Call Us</small><strong>970555018240</strong></div>
  </div>
  <div class="abs logo"><i class="mark"></i><span>Brightwell Supports</span></div>
  <div class="abs social"><i></i><i></i><i></i><i></i></div>

  <nav class="abs nav">
    <a class="active">Home</a><a>Services</a><a>Residential Program</a><a>Day/Employment Program</a><a>SLS Program</a><a>Employee Resources</a><a>Our Team</a><a>Contact Us</a>
  </nav>

  <section class="abs hero" role="img" aria-label="Photo of a man on a rocky peak pulling a climber up by rope">
    <div class="rock"></div>
    <span class="arrow" style="left:10px"></span>
    <span class="arrow" style="right:10px"></span>
    <div class="caption">Building Abilities ~ Creating Opportunities ~ Developing Relationships</div>
  </section>

  <h2 style="top:421px">Welcome to Brightwell Supports</h2>
  <p class="abs intro">Brightwell Supports is an agency designed to creatively serve individuals with developmental disabilities in community-based settings throughout Colorado. Brightwell Supports is an approved service agency through the Division of Developmental Disabilities. Mission Statement: To promote relationships, attachment, positive boundaries, and resource development to create opportunities and improve the lives of people living with disabilities.</p>

  <h2 style="top:513px">Brightwell Supports Values</h2>
  <section class="abs values">
    <span class="chev" style="left:2px">‹</span><span class="chev" style="right:4px">›</span>
    <div class="card" style="left:18px"><div class="ph" role="img" aria-label="Photo of a businessman drawing a large light bulb" style="background:linear-gradient(#9ea2a8,#6f747a)"></div><h3>Community Integration</h3><p>Promoting "connected independence" for individuals to continually develop necessary skills</p></div>
    <div class="card" style="left:171px"><div class="ph" role="img" aria-label="Photo of a mountain stream through pine forest" style="background:linear-gradient(#a9c3dc 0%,#4d6e45 55%,#7a8a70 100%)"></div><h3>Therapeutic Attachment</h3><p>Promoting "connected independence" for individuals to continually develop necessary skills</p></div>
    <div class="card" style="left:323px"><div class="ph" role="img" aria-label="Photo of a hand drawing a bridge for a man leaping between cliffs" style="background:linear-gradient(#d7dde3,#9aa0a6)"></div><h3>Positive Boundaries</h3><p>Promoting "connected independence" for individuals to continually develop necessary skills</p></div>
    <div class="card" style="left:476px"><div class="ph" role="img" aria-label="Photo of hands reaching toward hanging light bulbs" style="background:linear-gradient(#55585c,#2e3033)"></div><h3>Meaningful Connections</h3><p>Promoting "connected independence" for individuals to continually develop necessary skills</p></div>
  </section>

  <h2 style="top:784px">Client Supports</h2>

  <div class="support" style="left:12px;top:826px">
    <svg width="36" height="30" viewBox="0 0 36 30"><circle cx="11" cy="8" r="6" fill="#8b2a2b"/><path d="M0 29c0-9 5-13 11-13s11 4 11 13z" fill="#8b2a2b"/><circle cx="25" cy="10" r="5" fill="#8b2a2b"/><path d="M20 29c0-8 2-11 6-11s9 3 9 11z" fill="#8b2a2b"/></svg>
    <div><h4>Client Advisory Board</h4><p>Brightwell Supports receives feedback and direction from a group of individuals comprised of persons served.</p></div>
  </div>
  <div class="support" style="left:233px;top:826px">
    <svg width="28" height="28" viewBox="0 0 28 28"><circle cx="14" cy="14" r="11" fill="none" stroke="#8b2a2b" stroke-width="5"/><circle cx="14" cy="14" r="11" fill="none" stroke="#fff" stroke-width="5" stroke-dasharray="4 13.3" stroke-dashoffset="2"/></svg>
    <div><h4>Recreational Support</h4><p>Brightwell Supports receives feedback and direction from a group of individuals comprised of persons served.</p></div>
  </div>
  <div class="support" style="left:448px;top:826px">
    <svg width="30" height="30" viewBox="0 0 30 30"><path d="M20 4H3v24h22V12" fill="none" stroke="#8b2a2b" stroke-width="3"/><path d="M12 19l2-6 12-12 4 4-12 12z" fill="#8b2a2b"/></svg>
    <div><h4>Integrated Treatment Plans</h4><p>Brightwell Supports receives feedback and direction from a group of individuals comprised of persons served.</p></div>
  </div>
  <div class="support" style="left:12px;top:902px">
    <svg width="32" height="30" viewBox="0 0 32 30"><rect x="2" y="4" width="28" height="25" rx="2" fill="none" stroke="#8b2a2b" stroke-width="2"/><line x1="9" y1="1" x2="9" y2="7" stroke="#8b2a2b" stroke-width="2"/><line x1="23" y1="1" x2="23" y2="7" stroke="#8b2a2b" stroke-width="2"/><g fill="#8b2a2b"><rect x="7" y="12" width="4" height="4"/><rect x="14" y="12" width="4" height="4"/><rect x="21" y="12" width="4" height="4"/><rect x="7" y="20" width="4" height="4"/><rect x="14" y="20" width="4" height="4"/><rect x="21" y="20" width="4" height="4"/></g></svg>
    <div><h4>Personal Goal Plans</h4><p>Brightwell Supports receives feedback and direction from a group of individuals comprised of persons served.</p></div>
  </div>
  <div class="support" style="left:233px;top:902px">
    <svg width="28" height="28" viewBox="0 0 28 28"><circle cx="14" cy="8" r="6" fill="#8b2a2b"/><path d="M3 27c0-8 5-12 11-12s11 4 11 12z" fill="#8b2a2b"/></svg>
    <div><h4>Trained Providers</h4><p>Brightwell Supports receives feedback and direction from a group of individuals comprised of persons served.</p></div>
  </div>
  <div class="support" style="left:448px;top:902px">
    <svg width="28" height="32" viewBox="0 0 28 32"><path d="M14 2a10 10 0 0 0-6 18v5h12v-5A10 10 0 0 0 14 2z" fill="none" stroke="#8b2a2b" stroke-width="2"/><rect x="10" y="27" width="8" height="3" fill="#8b2a2b"/><path d="M14 8l-3 7h6z" fill="#8b2a2b"/></svg>
    <div><h4>On-site classes</h4><p>Brightwell Supports receives feedback and direction from a group of individuals comprised of persons served.</p></div>
  </div>

  <footer class="abs footer">
    <h5 style="left:12px">Contact Us</h5>
    <ul style="left:12px;top:48px">
      <li><span>⚲</span><span>418 Alder Ridge Road<br>Larkfield, CO 80599</span></li>
      <li><span>☏</span><span>Phone: 720-555-0148 &nbsp;Fax:303-555-0192</span></li>
      <li><span>✉</span><span>Mail: hello@brightwellmail.org</span></li>
    </ul>
    <h5 style="left:221px">Latest Tweets</h5>
    <ul style="left:221px;top:47px;width:160px">
      <li style="margin-bottom:6px"><span>›</span><span>Aenean lacinia bibendum nulla sed leo posuere erat a ante venenatis dapibus <a>@brightnote.org.</a></span></li>
      <li><span>›</span><span>Donec ullamcorper metus auctor fringilla. Nullam <a>@LarkfieldNews</a></span></li>
    </ul>
    <h5 style="left:445px">Latest Blog posts</h5>
    <ul style="left:445px;top:48px;width:200px;line-height:13.5px">
      <li style="margin-bottom:14px;gap:14px"><div class="thumb" role="img" aria-label="Blog post photo" style="background:linear-gradient(#c9a27c,#7a5a3e)"></div><span>Vivamus sagittis lacus vel augue leet rutrum dolor auctor.<br><span class="time">3 week ago</span></span></li>
      <li style="gap:14px"><div class="thumb" role="img" aria-label="Blog post landscape photo" style="background:linear-gradient(#6d8fa8,#2f4a3a)"></div><span>Vivamus sagittis lacus vel augue leet rutrum dolor auctor.<br><span class="time">3 week ago</span></span></li>
    </ul>
  </footer>
  <div class="abs base">
    <p>Content copyright 2014. Brightwell Supports. All rights reserved.</p>
    <span class="ring" style="left:512px"></span><span class="ring" style="left:546px"></span><span class="ring" style="left:581px"></span><span class="ring" style="left:615px"></span>
  </div>
</div>
</body>
</html>
```